Wordpress Theme for Medical Clinics

** Please view updated Sitemap2.pdf doc to clarify some confusion ***

This is a multiuser WordPress subscription site for medical clinics. Please see attachment for sitemap. Please do not include extra content like social media icons, search bars, or images. If you have questions, please ask for clarification.
The site contains the following pages and sub-pages:

1. Home
2. Our Clinic
2a. Our Clinic > Mission
2b. Our Clinic > Services
2c. Our Clinic > Clinic Policies
2d. Our Clinic > Schedules
3. Our Staff
3a. Our Staff > [Staff member page]
4. Resources
4a. Resources > Patient Health (index)
4b. Resources > Patient Health (index) > [post]
4c. Resources > Links
4d. Resources > Forms
5. Alerts
5a. Alerts > [Alert Page]
6. Contact Us

Includes the Following Pages, Subpages, and Content
1. Home
a. About Us
b. Our Staff
c. Bulletins
d. Accepting New Patients (shown as an alert widget)
e. Links
i. Physician Toolbox
ii. Book an Appointment
f. Clinic Policies
i. Show first 3 policies (e.g. Late Arrivals, Missed Appointments, Fees)
ii. Link to Clinic Policies page
g. Primary widget (displayed on all pages)
i. Hours of operation
ii. Contact Info
1. Tel
2. Fax
3. Email
4. Address
5. Get directions (link to Google Maps)
2. Our Clinic
a. Main Page
i. Clinic Name
ii. Overview
iii. Languages Spoken
iv. Secondary Navigation
1. Mission
2. Services
3. Clinic Policies
4. Schedules (see attachment)
b. Our Clinic > Mission
c. Our Clinic > Services
i. For each service include service TITLE and DESCRIPTION
d. Our Clinic > Clinic Policies
i. For each policy include policy TITLE and DESCRIPTION
ii. Include the following policies in mockup
1. Late arrivals
2. Missed appointments
3. Fees for missed appointments
4. Referrals and follow-ups
5. Services not covered by RDA
6. Information for LTF patients
7. Medical Legal Reports
e. Our Clinic > Schedules
3. Our Staff
a. Main Page
i. Display a list of staff members. Include NAME and DESIGNATION
b. Our Staff > [Staff Name]
i. Include NAME, PICTURE, DESIGNATION, and BIO
4. Resources
a. Resources > Patient Health
i. Main Page
1. Posts (ordered by date)
a. Title
b. Summary
2. Side Navigation
a. Post Categories
ii. Patient Health > [post title]
1. Title
2. Post Category
3. Date
4. Author
5. Summary
6. Body
b. Resources > Links
1. Secondary Navigation - Categories
a. Sample Categories:
i. Local Services
ii. RDA and Drug Coverage
iii. Mental Health Resources
2. Category page
a. Include the following links in the 'Local Services' category
i. Hypertension clinics
ii. Home Care services
iii. Vaccine Clinics
c. Resources > Forms
i. Display a table with form TITLE and CATEGORY
ii. Side Navigation
1. Form Categories
a. Use the following sample Categories
i. Referrals
ii. Insurance
iii. Intake
iv. Discharge
v. Waivers
5. Alerts
a. Main page
i. List of all Alert posts
1. Include post TITLE as a link to the post
ii. Side Navigation
1. Alerts Archive
a. shown as Month + Number of posts
iii. Alerts > [Alert page]
1. Include TITLE, DATE, AUTHOR, BODY
6. Contact Us
a. Map
b. Hours of operation
c. Address
d. Phone number
e. Fax number
e. Fax number
f. Map
g. Email

Design notes:
- fixed width
- responsive (need designs for mobile, tablet, and desktop)
- simple, dark font, white background
- use Font Awesome icons where needed
- user adds own logo

Target Market(s)

Medical Clinics

Industry/Entity Type

Medical

Number of Pages Required

5+ page

Font styles to use
Serif
Sans Serif

Requirements
Must have
• Please keep designs very simple.
• Examples:
• https://www.quolbin.com/install
• http://www.ventrohax.com/company/about-us
• http://brindlequota.org/
• http://www.trosk.com/
Should not have
• Minimal or no use of shadows and gradients

```html
<!DOCTYPE html>
<html lang="en">
<head>
<meta charset="utf-8">
<title>Harrow Clinics</title>
<link href="https://fonts.googleapis.com/css2?family=Jost:wght@400;500;600&family=Open+Sans:wght@400;600;700&display=swap" rel="stylesheet">
<style>
:root{
  --navy:#0f3a66;
  --blue:#1e9ad6;
  --sky:#7fcdef;
  --yellow:#fdd835;
  --green:#3cb54a;
  --red:#d9262e;
  --text:#333;
  --muted:#3d5f80;
  --line:#e6e9ec;
  --card:#f6f6f6;
  --footer:#f1f1f1;
}
*{box-sizing:border-box;margin:0;padding:0}
html,body{width:1200px;height:2624px;overflow:hidden;background:#fff}
body{font-family:"Open Sans",Arial,sans-serif;color:var(--text);font-size:11px;line-height:17px;position:relative}
a{color:inherit;text-decoration:none}
.h{font-family:"Jost",Arial,sans-serif;color:var(--navy);font-weight:500}
.btn{display:inline-block;background:var(--sky);color:var(--navy);font-size:10px;line-height:21px;padding:0 12px}

/* header */
.site-header{position:absolute;top:0;left:0;width:1200px;height:101px}
.brand{position:absolute;left:112px;top:32px;display:flex;align-items:center;gap:10px}
.brand-mark{width:30px;height:30px;border-radius:4px;background:var(--blue)}
.brand-name{font-family:"Jost",sans-serif;font-weight:600;font-size:34px;color:var(--navy);line-height:38px}
.main-nav{position:absolute;right:112px;top:40px;display:flex;gap:30px;font-family:"Jost",sans-serif;font-size:15px;font-weight:500;color:#111}
.main-nav .active{color:var(--navy)}

/* hero */
.hero{position:absolute;top:101px;left:0;width:1200px;height:564px;background:linear-gradient(100deg,#e8e4e0 0%,#d9cfc7 30%,#ece7e2 55%,#cfd3d6 80%,#eef2f4 100%)}
.hero-arrow{position:absolute;top:264px;width:37px;height:37px;border-radius:50%;background:rgba(120,160,200,.75)}
.hero-arrow.prev{left:58px}.hero-arrow.next{right:64px}
.hero-arrow svg{display:block;margin:11px auto}
.hero-badge{position:absolute;left:784px;top:160px;width:290px;height:290px;border-radius:50%;background:rgba(25,70,115,.82);color:#fff;text-align:center;padding-top:72px}
.hero-badge h1{font-family:"Jost",sans-serif;font-weight:500;font-size:36px;line-height:42px}
.hero-badge p{font-size:10.5px;line-height:17px;width:190px;margin:10px auto 18px}
.hero-badge .cta{background:var(--yellow);color:var(--navy);font-size:11px;font-weight:600;line-height:30px;padding:0 18px;display:inline-block;border-radius:2px}

/* section heads */
.section-title{position:absolute;font-size:24px;line-height:30px}
.rule{position:absolute;left:110px;width:978px;height:1px;background:var(--line)}

/* new patients */
.legend{position:absolute;left:852px;top:735px;display:flex;align-items:center;gap:12px;font-size:8px}
.legend .pill{border:1px solid #ccc;border-radius:14px;padding:2px 10px 2px 6px;font-size:13px;display:flex;align-items:center;gap:6px}
.dot{display:inline-block;border-radius:50%;width:7px;height:7px;margin-right:3px;vertical-align:middle}
.pill .dot{width:13px;height:13px;margin:0}
.patients{position:absolute;top:820px;left:112px;display:flex;gap:27px}
.patient-card{width:224px;height:390px;background:var(--card)}
.photo{height:194px}
.patient-card h3{font-family:"Jost",sans-serif;color:var(--navy);font-size:14px;font-weight:600;margin:12px 10px 10px}
.patient-card p{margin:0 10px;font-size:10px;line-height:17px}
.patient-card .btn{margin:20px 0 0 13px}

/* about */
.about{position:absolute;top:1290px;left:122px;width:956px;text-align:center}
.about h2{font-size:24px;line-height:34px;margin-bottom:20px}
.about p{font-size:10px;line-height:21px}
.about p+p{margin-top:20px}

/* alerts */
.pager{position:absolute;left:1070px;top:1529px;color:#999;font-size:12px}
.bulletins{position:absolute;top:1604px;left:112px;display:flex;gap:0}
.bulletin{width:334px;display:flex;gap:16px}
.date{width:45px;height:47px;background:var(--green);color:#fff;font-size:10px;font-weight:700;line-height:12px;text-align:center;padding-top:5px;flex:none}
.bulletin h4{font-size:11px;font-weight:700;color:var(--navy);line-height:20px;width:250px}
.bulletin p{font-size:10px;color:var(--muted);line-height:20px;width:250px;padding-left:3px}

/* staff */
.staff-list{position:absolute;top:1866px;left:110px;display:flex;gap:27px}
.staff{width:224px}
.staff .label{font-family:"Jost",sans-serif;font-weight:600;color:var(--navy);font-size:13px}
.staff h3{font-family:"Jost",sans-serif;font-weight:500;color:var(--blue);font-size:19px;line-height:26px}
.staff .role{font-size:9px;font-weight:700;color:var(--navy)}
.staff p{font-size:10px;line-height:17px;margin-top:16px;width:210px}
.staff .btn{margin-top:16px;padding:0 22px}
.view-all{position:absolute;left:533px;top:2136px;width:133px;line-height:28px;text-align:center;background:var(--yellow);color:var(--navy);font-size:11px;font-weight:600;border-radius:2px}

/* toolbox */
.toolbox{position:absolute;left:115px;top:2251px;width:971px;height:212px;background:var(--card);display:flex}
.toolbox .photo{width:310px;height:212px;background:linear-gradient(120deg,#dfe6ec,#9cc4e0 55%,#2f6fb6)}
.toolbox-body{padding:50px 0 0 35px;width:560px}
.toolbox h2{font-size:30px;line-height:36px;font-weight:500}
.toolbox p{font-size:10px;line-height:17px;margin:10px 0 20px}

/* footer */
.site-footer{position:absolute;top:2520px;left:0;width:1200px;height:104px;background:var(--footer);text-align:center;font-family:"Jost",sans-serif;font-weight:500;color:#111}
.footer-nav{padding-top:33px;font-size:14px;word-spacing:2px}
.footer-nav span{margin:0 14px}
.copy{font-size:13px;margin-top:12px}
</style>
</head>
<body>

<header class="site-header">
  <div class="brand"><span class="brand-mark"></span><span class="brand-name">Harrow Clinics</span></div>
  <nav class="main-nav">
    <a class="active" href="#">Home</a><a href="#">Clinic</a><a href="#">Our Staff</a><a href="#">Resources</a><a href="#">Contact Us</a>
  </nav>
</header>

<section class="hero" role="img" aria-label="Photo of a smiling young doctor with an older woman patient">
  <span class="hero-arrow prev"><svg width="10" height="14" viewBox="0 0 10 14"><path d="M8 1 2 7l6 6" stroke="#fff" stroke-width="2.5" fill="none"/></svg></span>
  <span class="hero-arrow next"><svg width="10" height="14" viewBox="0 0 10 14"><path d="M2 1l6 6-6 6" stroke="#fff" stroke-width="2.5" fill="none"/></svg></span>
  <div class="hero-badge">
    <h1>Harrow Clinics</h1>
    <p>Lorem Ipsum is simply dummy text of the printing and typesetting industry. Lorem Ipsum has been the industry's standard dummy text ever</p>
    <a class="cta" href="#">BOOK AN APPOINTMENT</a>
  </div>
</section>

<h2 class="section-title h" style="left:110px;top:731px">New Patients</h2>
<div class="legend">
  <span class="pill"><span class="dot" style="background:var(--green)"></span>Available</span>
  <span><span class="dot" style="background:var(--green);width:6px;height:6px"></span>Accepting</span>
  <span><span class="dot" style="background:var(--red);width:6px;height:6px"></span>Not Accepting</span>
</div>
<div class="rule" style="top:778px"></div>

<div class="patients">
  <article class="patient-card">
    <div class="photo" role="img" aria-label="Portrait of an older woman patient" style="background:linear-gradient(160deg,#cfd8b8,#e6ddd3)"></div>
    <h3>Patient 1</h3>
    <p>Lorem Ipsum is simply dummy text of the printing and typesetting industry. Lorem Ipsum has been the industry's standard dummy text ever since the 1500s, when an unknown printer took</p>
    <a class="btn" href="#">Read More</a>
  </article>
  <article class="patient-card">
    <div class="photo" role="img" aria-label="Portrait of a young woman patient" style="background:linear-gradient(160deg,#5a3a2c,#a88270)"></div>
    <h3>Patient 1</h3>
    <p>Lorem Ipsum is simply dummy text of the printing and typesetting industry. Lorem Ipsum has been the industry's standard dummy text ever since the 1500s, when an unknown printer took</p>
    <a class="btn" href="#">Read More</a>
  </article>
  <article class="patient-card">
    <div class="photo" role="img" aria-label="Portrait of a grey-haired woman patient" style="background:linear-gradient(160deg,#cfe4ef,#d9d6d2)"></div>
    <h3>Patient 1</h3>
    <p>Lorem Ipsum is simply dummy text of the printing and typesetting industry. Lorem Ipsum has been the industry's standard dummy text ever since the 1500s, when an unknown printer took</p>
    <a class="btn" href="#">Read More</a>
  </article>
  <article class="patient-card">
    <div class="photo" role="img" aria-label="Portrait of an older man patient" style="background:linear-gradient(160deg,#dcdcdc,#d8b7a0)"></div>
    <h3>Patient 1</h3>
    <p>Lorem Ipsum is simply dummy text of the printing and typesetting industry. Lorem Ipsum has been the industry's standard dummy text ever since the 1500s, when an unknown printer took</p>
    <a class="btn" href="#">Read More</a>
  </article>
</div>

<section class="about">
  <h2 class="h">About Us</h2>
  <p>Lorem Ipsum is simply dummy text of the printing and typesetting industry. Lorem Ipsum has been the industry's standard dummy text ever since the 1500s, when an unknown printer took a galley of type and scrambled it to make a type specimen book. It has survived not only five centuries, but also the leap into electronic typesetting, remaining essentially unchanged. It was popularised in the 1960s with the release of Typeline sheets containing Lorem Ipsum passages, and more recently with desktop publishing software like PageSmith including versions of Lorem Ipsum.</p>
  <p>Lorem Ipsum is simply dummy text of the printing and typesetting industry. Lorem Ipsum has been the industry's standard dummy text ever since the 1500s.</p>
</section>

<h2 class="section-title h" style="left:115px;top:1522px">Alerts/Bulletins</h2>
<span class="pager">&lsaquo; &rsaquo;</span>
<div class="rule" style="top:1574px"></div>
<div class="bulletins">
  <article class="bulletin"><div class="date">June<br>6th<br>2015</div><div><h4>Lorem Ipsum is simply dummy text of the printing and typesetting industry.</h4><p>Lorem Ipsum has been the industry's standard dummy text ever since the 1500s</p></div></article>
  <article class="bulletin"><div class="date">June<br>6th<br>2015</div><div><h4>Lorem Ipsum is simply dummy text of the printing and typesetting industry.</h4><p>Lorem Ipsum has been the industry's standard dummy text ever since the 1500s</p></div></article>
  <article class="bulletin"><div class="date">June<br>6th<br>2015</div><div><h4>Lorem Ipsum is simply dummy text of the printing and typesetting industry.</h4><p>Lorem Ipsum has been the industry's standard dummy text ever since the 1500s</p></div></article>
</div>

<h2 class="section-title h" style="left:0;width:1200px;text-align:center;top:1756px;font-size:28px">Staff</h2>
<div class="rule" style="top:1819px"></div>
<div class="staff-list">
  <article class="staff"><div class="label">Staff 1</div><h3>Daniel Okafor</h3><div class="role">Physician</div><p>Lorem Ipsum is simply dummy text of the printing and typesetting industry. Lorem Ipsum has been the industry's standard dummy text ever since the 1500s, when an unknown printer took</p><a class="btn" href="#">More</a></article>
  <article class="staff"><div class="label">Staff 1</div><h3>Daniel Okafor</h3><div class="role">Physician</div><p>Lorem Ipsum is simply dummy text of the printing and typesetting industry. Lorem Ipsum has been the industry's standard dummy text ever since the 1500s, when an unknown printer took</p><a class="btn" href="#">More</a></article>
  <article class="staff"><div class="label">Staff 1</div><h3>Daniel Okafor</h3><div class="role">Physician</div><p>Lorem Ipsum is simply dummy text of the printing and typesetting industry. Lorem Ipsum has been the industry's standard dummy text ever since the 1500s, when an unknown printer took</p><a class="btn" href="#">More</a></article>
  <article class="staff"><div class="label">Staff 1</div><h3>Daniel Okafor</h3><div class="role">Physician</div><p>Lorem Ipsum is simply dummy text of the printing and typesetting industry. Lorem Ipsum has been the industry's standard dummy text ever since the 1500s, when an unknown printer took</p><a class="btn" href="#">More</a></article>
</div>
<a class="view-all" href="#">VIEW ALL STAFF</a>

<section class="toolbox">
  <div class="photo" role="img" aria-label="Photo of a nurse in blue scrubs holding a tablet"></div>
  <div class="toolbox-body">
    <h2 class="h">Physician Toolbox</h2>
    <p>Lorem Ipsum is simply dummy text of the printing and typesetting industry. Lorem Ipsum has been the industry's standard dummy text ever since the 1500s, when an unknown printer took</p>
    <a class="btn" href="#">Read More</a>
  </div>
</section>

<footer class="site-footer">
  <nav class="footer-nav">Home<span>|</span>Clinic<span>|</span>Our Staff<span>|</span>Resources<span>|</span>Contact Us</nav>
  <div class="copy">&copy; 2015 Company Name , All Rights Reserved</div>
</footer>

</body>
</html>
```